Upmarket Dessert Lounge needs a Business Card Design

We are an upmarket dessert lounge needing a business card to match our image.

We want something that is simple yet beautiful, feminine, classy, sophisticated and elegant. We want it to stand out and don't mind if it is bold.

The design should include our logo and colours of red or maroon with gold highlights. We don't mind if black is used.

Marlow & Quince

Target Market(s)

For those who like to indulge or treat themselves and give in to their temptations on good quality desserts.

Industry/Entity Type

Business

Requirements
Must have
• Must include our logo and our name

Marlow & Quince

M & Q

```html
<!DOCTYPE html>
<html lang="en">
<head>
<meta charset="utf-8">
<title>Marlow &amp; Quince — Business Card</title>
<link rel="stylesheet" href="https://fonts.googleapis.com/css2?family=Source+Sans+3:wght@400;600;700&display=swap">
<style>
  :root {
    --maroon: #7a1518;
    --ink: #4a4a4a;
    --ornament: #eee3e5;
    --card: #ffffff;
    --stage: #ece8e4;
    --divider: #b98a72;
  }
  * { box-sizing: border-box; margin: 0; padding: 0; }
  html, body { width: 1200px; height: 402px; overflow: hidden; }
  body {
    background: var(--stage);
    font-family: "Source Sans 3", "Myriad Pro", Arial, sans-serif;
    position: relative;
  }
  .card {
    position: absolute;
    top: 56px;
    width: 540px;
    height: 290px;
    background: var(--card);
    overflow: hidden;
    box-shadow: 0 2px 6px rgba(0,0,0,0.12);
  }
  .card--front { left: 45px; }
  .card--back { left: 615px; }
  .ornament-band {
    position: absolute;
    left: 0;
    width: 100%;
    height: 46px;
    background: linear-gradient(to bottom, var(--ornament), #f7f1f2);
  }
  .ornament-band--top { top: 0; }
  .ornament-band--bottom { bottom: 0; background: linear-gradient(to top, var(--ornament), #f7f1f2); }

  .brand-name {
    position: absolute;
    left: 0;
    top: 0;
    width: 250px;
    height: 290px;
    display: flex;
    align-items: center;
    justify-content: center;
    color: var(--maroon);
    font-weight: 600;
    font-size: 26px;
    letter-spacing: 0.5px;
  }
  .divider {
    position: absolute;
    left: 250px;
    top: 58px;
    width: 2px;
    height: 175px;
    background: linear-gradient(to bottom, transparent, var(--divider) 30%, var(--divider) 70%, transparent);
  }
  .details {
    position: absolute;
    left: 279px;
    top: 58px;
    color: var(--ink);
    font-size: 13.5px;
    line-height: 1.2;
  }
  .person { color: var(--maroon); font-size: 18px; font-weight: 700; margin-bottom: 22px; }
  .person .title { font-size: 14px; font-weight: 400; }
  .address { margin-bottom: 40px; }
  .contact-list { list-style: none; }
  .contact-list li { display: flex; align-items: center; gap: 5px; height: 17px; }
  .contact-list svg { width: 10px; height: 10px; fill: var(--maroon); flex: none; }

  .monogram {
    position: absolute;
    inset: 0;
    display: flex;
    align-items: center;
    justify-content: center;
    color: var(--maroon);
    font-weight: 600;
    font-size: 64px;
  }
</style>
</head>
<body>
  <section class="card card--front">
    <div class="ornament-band ornament-band--top" role="img" aria-label="Faint pink floral scroll border"></div>
    <div class="ornament-band ornament-band--bottom" role="img" aria-label="Faint pink floral scroll border"></div>
    <div class="brand-name">Marlow &amp; Quince</div>
    <div class="divider"></div>
    <div class="details">
      <p class="person">Your name, <span class="title">Title</span></p>
      <p class="address">Street Name, City Name<br>State Zip Code</p>
      <ul class="contact-list">
        <li><svg viewBox="0 0 10 10"><path d="M2 0.5 L3.8 2.6 L2.9 3.7 Q4 6 6.3 7.1 L7.4 6.2 L9.5 8 L8.2 9.5 Q3.5 9 0.5 1.8 Z"/></svg>555-014-2270</li>
        <li><svg viewBox="0 0 10 10"><path d="M2.5 0 H7.5 V10 H2.5 Z M3.3 1 V7 H6.7 V1 Z M4.5 8 H5.5 V9 H4.5 Z" fill-rule="evenodd"/></svg>555-014-2270</li>
        <li><svg viewBox="0 0 10 10"><path d="M0 2 H10 V8.5 H0 Z M0.6 2.3 L5 5.6 L9.4 2.3" fill-rule="evenodd"/><path d="M0.5 2.5 L5 5.8 L9.5 2.5" stroke="#fff" stroke-width="0.8" fill="none"/></svg>info@marlowquince.com</li>
        <li><svg viewBox="0 0 10 10"><circle cx="5" cy="5" r="4.5" fill="none" stroke="#7a1518" stroke-width="1"/><path d="M0.5 5 H9.5 M5 0.5 V9.5" stroke="#7a1518" stroke-width="0.8"/><ellipse cx="5" cy="5" rx="2" ry="4.5" fill="none" stroke="#7a1518" stroke-width="0.8"/></svg>www.marlowquince.com</li>
      </ul>
    </div>
  </section>

  <section class="card card--back">
    <div class="ornament-band ornament-band--top" role="img" aria-label="Faint pink floral scroll border"></div>
    <div class="ornament-band ornament-band--bottom" role="img" aria-label="Faint pink floral scroll border"></div>
    <div class="monogram">M &amp; Q</div>
  </section>
</body>
</html>
```